Tusk Hollow Lodge website (design only)

Tusk Hollow Lodge (http://www.tuskhollowlodge-mw.example) is a private Safari lodge located in Malawi.
We would like a modern, professional website designed that does not subscribe to the cliched view of a Safari in Africa, but still maintain a wildlife/safari atmosphere.

The aim of our website is to entice people & drive them to the booking form.

Here are some examples of websites that we like. Although we would like our site to be a bit more in line with modern web design trends.

http://www.marulaplains.example/
http://www.kovunde.example/
http://www.tembalorecamp.example/

Requirements
Must have
• Here is a list of the pages required. Most of them will follow a standard content layout. I.e. heading, body and images.

If you take a look at the website, you will get an idea of hoe many page types there are +- 5

http://www.tuskhollowlodge-mw.example/index.htm

About Tusk Hollow
Lirundu Country Club
Rooms
Conferences
Cuisine
Facilities
Your Safari
Activities
Rates & Special Offers
Booking form
Latest Developments
How To Get There
Gallery
Contact Us
Blog / Newsfeed

```html
<!DOCTYPE html>
<html lang="en">
<head>
<meta charset="utf-8">
<title>Tusk Hollow Lodge</title>
<link rel="stylesheet" href="https://fonts.googleapis.com/css2?family=Arimo:ital,wght@0,400;0,700;1,400;1,700&family=Dosis:wght@400&family=Philosopher:ital@0;1&display=swap">
<style>
:root{
  --page:#d8d3d3;
  --nav:#1e1e1e;
  --green:#6c9c14;
  --green-light:#7dbb45;
  --field:#5ea12e;
  --panel:#ecede0;
  --strip:#f3f3f3;
  --dark:#2a2623;
  --bar:#9a9595;
  --text:#777;
  --foot:#555;
  --blue-top:#8cbcf0;
  --blue-bot:#3f7cd2;
  --white:#fff;
}
*{margin:0;padding:0;box-sizing:border-box}
html,body{width:816px;height:1200px;overflow:hidden}
body{background:var(--page);position:relative;font-family:Arimo,Arial,sans-serif;color:var(--text)}
.abs{position:absolute}
.hero{left:0;top:0;width:816px;height:348px;
  background:
   radial-gradient(ellipse 260px 180px at 560px 120px,rgba(245,238,220,.95),rgba(245,238,220,0) 70%),
   linear-gradient(180deg,#cfc7b4 0%,#a39a80 35%,#5d5a3e 60%,#3a3d24 80%,#2e3120 100%)}
.main-nav{left:0;top:24px;width:816px;height:46px;background:rgba(25,25,25,.88);display:flex;align-items:center;padding-left:32px}
.main-nav a{font-family:Dosis,sans-serif;color:var(--white);font-size:15px;text-decoration:none;margin-right:26px;letter-spacing:.2px;white-space:nowrap}
.brand{left:23px;top:77px;width:186px;height:206px;background:linear-gradient(160deg,#7aab1c,var(--green) 60%,#5b8910);text-align:center;font-family:Philosopher,sans-serif;font-style:italic;color:var(--white)}
.brand-name{font-size:27px;line-height:26px;margin-top:31px}
.brand-place{font-size:19px;line-height:30px;margin-top:34px}
.icon-bar{left:0;top:296px;width:536px;height:52px;background:rgba(120,120,120,.78)}
.icon-item{position:absolute;top:2px;width:70px;text-align:center;color:var(--white);font-size:11px;white-space:nowrap}
.icon-item svg{display:block;margin:0 auto 2px}
.booking{left:537px;top:238px;width:243px;height:143px;background:var(--white);box-shadow:0 2px 4px rgba(0,0,0,.35);font-family:Philosopher,sans-serif;z-index:5}
.booking h2{height:24px;background:var(--green-light);color:var(--white);font-weight:400;font-style:italic;font-size:14px;padding:3px 0 0 16px}
.field{position:absolute;border:1.5px solid var(--field);height:14px;font-size:9px;font-style:italic;color:#555;padding-left:3px;line-height:11px}
.lbl{position:absolute;font-size:8px;font-style:italic;color:#444;white-space:nowrap}
.lbl small{font-size:5px;letter-spacing:-.1px}
.cal{position:absolute;width:10px;height:10px;border:1px solid #b55;background:#f4d8d8}
.submit{position:absolute;left:183px;top:116px;width:50px;height:14px;background:var(--field);color:var(--white);font-size:9px;font-style:italic;text-align:center;line-height:14px}
.strip{left:26px;top:348px;width:763px;height:52px;background:var(--strip);border-bottom:3px solid #e0e0e0}
.content{left:26px;top:401px;width:763px;height:305px;background:var(--panel)}
.welcome{left:45px;top:410px;width:477px;height:271px;border:1px solid #cfd3c6;outline:1px solid #e2e4da;outline-offset:-4px;padding:20px 20px 0 17px}
.welcome h1{font-size:11.5px;color:#4f7a21;font-weight:700;margin-bottom:18px}
.welcome p{font-size:9.6px;line-height:14.6px;text-align:justify;padding-left:4px}
.welcome p.lead{color:#111;font-style:italic;margin:4px 0 6px}
.welcome .more{text-align:right;color:#6aa72c}
.enquire{left:551px;top:412px;width:214px;height:119px;background:linear-gradient(180deg,#8c9a6a,#6e8a3a 55%,#5d7a2c);box-shadow:3px 3px 5px rgba(0,0,0,.4);font-family:Philosopher,sans-serif;color:var(--white);font-size:21px;line-height:22px;text-align:center;padding-top:65px;text-shadow:0 1px 2px rgba(0,0,0,.5)}
.social-btn{left:553px;width:218px;height:35px;border-radius:18px;background:linear-gradient(180deg,var(--blue-top),var(--blue-bot));color:var(--white);font-weight:700;font-size:15px;line-height:35px;padding-left:46px;box-shadow:0 1px 2px rgba(0,0,0,.3);white-space:nowrap}
.social-btn::before{content:"";position:absolute;left:10px;top:7px;width:21px;height:21px;border-radius:50%;background:rgba(255,255,255,.35)}
.facilities{left:26px;top:706px;width:763px;height:286px;background:var(--dark)}
.facility{position:absolute;top:729px;width:164px}
.facility .photo{width:164px;height:124px;border:4px solid var(--white)}
.facility h3{font-size:11px;font-style:italic;font-weight:700;color:var(--white);margin:28px 0 6px 3px}
.facility p{font-size:10.8px;line-height:14.5px;color:#eee;text-align:justify;padding:0 2px;hyphens:auto;-webkit-hyphens:auto}
.divider{position:absolute;top:722px;width:1px;height:250px;background:#5a5450}
.bottom-bar{left:26px;top:992px;width:763px;height:32px;background:var(--bar);color:var(--white);font-size:8.5px;text-align:right;padding:12px 20px 0 0}
.footer-links{left:35px;top:1038px;font-size:8.3px;line-height:12.8px;color:var(--foot);list-style:none}
.blog{left:193px;top:1043px;width:186px;font-size:7.6px;line-height:11px;color:var(--foot)}
.blog h4{font-weight:400;font-size:8px;border-bottom:1px solid #aaa;margin-bottom:14px;width:186px}
.blog p{text-align:justify;margin-bottom:10px}
.blog b{font-weight:400;color:#222}
.office{left:449px;top:1043px;font-size:8px;line-height:11.5px;color:var(--foot);font-style:normal}
.office p{margin-bottom:7px}
.circles{left:627px;top:1034px;display:flex;gap:7px}
.circles span{width:25px;height:25px;border-radius:50%;background:#4a4a4a;display:block}
</style>
</head>
<body>

<div class="abs hero" role="img" aria-label="Misty morning forest with tall trees and sunlight"></div>

<nav class="abs main-nav">
  <a>About Tusk Hollow</a><a>Your Safari</a><a>Activities</a><a>Rates &amp; Special Offers</a><a>Latest Developments</a><a>How To Get There</a>
</nav>

<div class="abs brand">
  <div class="brand-name">Tusk Hollow<br>Lodge</div>
  <div class="brand-place">Kalinde Estate<br>Nsaluzi</div>
</div>

<div class="abs icon-bar">
  <div class="icon-item" style="left:12px"><svg width="32" height="30" viewBox="0 0 32 30"><path d="M16 2 2 15h4v13h8v-8h4v8h8V15h4z" fill="#7bbf3e"/></svg>Rooms</div>
  <div class="icon-item" style="left:89px"><svg width="32" height="30" viewBox="0 0 32 30"><rect x="11" y="1" width="10" height="17" rx="5" fill="#7bbf3e"/><path d="M7 13a9 9 0 0 0 18 0" stroke="#7bbf3e" stroke-width="2.5" fill="none"/><rect x="14.7" y="22" width="2.6" height="6" fill="#7bbf3e"/></svg>Conferences</div>
  <div class="icon-item" style="left:165px"><svg width="36" height="30" viewBox="0 0 36 30"><path d="M4 12h24v6a10 10 0 0 1-10 10h-4A10 10 0 0 1 4 18z" fill="#7bbf3e"/><path d="M28 14h3a4 4 0 0 1 0 8h-4" stroke="#7bbf3e" stroke-width="2.5" fill="none"/><path d="M12 9c-2-3 2-4 0-7M18 9c-2-3 2-4 0-7" stroke="#7bbf3e" stroke-width="1.5" fill="none"/></svg>Cuisine</div>
  <div class="icon-item" style="left:236px"><svg width="32" height="30" viewBox="0 0 32 30"><path d="M3 3h12v25H3zM17 3h12v25H17z" fill="#7bbf3e"/><path d="M21 3v10l2-2 2 2V3" fill="#4f8a25"/></svg>Facilities</div>
  <div class="icon-item" style="left:309px"><svg width="34" height="30" viewBox="0 0 34 30"><rect x="2" y="7" width="30" height="21" rx="3" fill="#7bbf3e"/><rect x="11" y="3" width="12" height="6" fill="#7bbf3e"/><circle cx="17" cy="17" r="6" fill="#4f8a25"/><circle cx="17" cy="17" r="3.5" fill="#7bbf3e"/></svg>Gallery</div>
  <div class="icon-item" style="left:382px"><svg width="32" height="30" viewBox="0 0 32 30"><path d="M7 2h13l7 7v19H7z" fill="#7bbf3e"/><path d="M20 2v7h7" fill="#4f8a25"/></svg>Our Blog</div>
  <div class="icon-item" style="left:456px"><svg width="32" height="30" viewBox="0 0 32 30"><path d="M18 2l10 10-4 1-5 5 1 5-3 1-4-5-7 7-1-1 7-7-5-4 1-3 5 1 5-5z" fill="#7bbf3e"/></svg>Contact Us</div>
</div>

<div class="abs strip"></div>
<div class="abs content"></div>

<form class="abs booking">
  <h2>Booking Request</h2>
  <div class="field" style="left:24px;top:31px;width:90px">Place</div>
  <div class="field" style="left:126px;top:31px;width:110px">Package Type</div>
  <div class="lbl" style="left:25px;top:51px">Journey Date</div>
  <div class="lbl" style="left:126px;top:51px">Return Date</div>
  <div class="field" style="left:24px;top:62px;width:72px"></div>
  <div class="cal" style="left:101px;top:64px"></div>
  <div class="field" style="left:126px;top:62px;width:72px"></div>
  <div class="cal" style="left:206px;top:64px"></div>
  <div class="lbl" style="left:20px;top:83px">Adult</div>
  <div class="lbl" style="left:93px;top:83px">Children<small>(above 3yrs)</small></div>
  <div class="lbl" style="left:170px;top:83px">Children<small>(below 3yrs)</small></div>
  <div class="field" style="left:20px;top:93px;width:29px"></div>
  <div class="field" style="left:93px;top:93px;width:29px"></div>
  <div class="field" style="left:170px;top:93px;width:29px"></div>
  <div class="submit">Submit</div>
</form>

<section class="abs welcome">
  <h1>Welcome to Tusk Hollow Lodge</h1>
  <p>Warmest welcome to the unique Malawi experience. lodge complex, game park, the 18 hole Lirundu golf club and Nkhoma dam.</p>
  <p class="lead">A multi million dollar development at Kalinde estate, Nsaluzi on Mpemba road 20 kms from Chisala Malawi's commercial capital creating a fascinating paradise for multiple leisure activities and conserving Malawi wildlife.Our Lodge also has beautifully designed and built in golden colored rock.</p>
  <p>The 1st phase was completed in 2007, and is approx 1800 sq. meters, comprising of:<br>A fully carpeted and elegantly furnished restaurant with seating for up to 80 guests and exceptional cuisine to completely satisfy most palates.<br>A stately carpeted conference hall for up to 45 people, 5 luxurious and spacious ensuite cottages with lounge and private verandah accessing a beautiful 18 meter swimming pool with cascading waterfall.</p>
  <p class="more">Read more</p>
</section>

<div class="abs enquire" role="img" aria-label="Zebra grazing on green grass">Enquire For A<br>Booking</div>
<div class="abs social-btn" style="top:568px">Sign in with Friendnest</div>
<div class="abs social-btn" style="top:618px">Sign in with Chirper</div>

<div class="abs facilities"></div>
<div class="divider" style="left:220px"></div>
<div class="divider" style="left:408px"></div>
<div class="divider" style="left:595px"></div>

<article class="facility" style="left:45px">
  <div class="photo" role="img" aria-label="Lodge building beside a swimming pool" style="background:linear-gradient(180deg,#c9d6e2 0%,#b7c3c8 30%,#8a5a45 45%,#6f7f4a 70%,#9a8a7a 100%)"></div>
  <h3>Facility 1</h3>
  <p>Lorem ipsum dolor sit amet, consectetur adipisicing elit, sed do eiusmod tempor incididunt ut labore et dolore magna aliqua.</p>
</article>
<article class="facility" style="left:233px">
  <div class="photo" role="img" aria-label="Restaurant hall with set tables" style="background:linear-gradient(180deg,#c7b37a 0%,#b8a272 40%,#8a3040 65%,#e6e0e0 100%)"></div>
  <h3>Facility 2</h3>
  <p>Lorem ipsum dolor sit amet, consectetur adipisicing elit, sed do eiusmod tempor incididunt ut labore et dolore magna aliqua.</p>
</article>
<article class="facility" style="left:420px">
  <div class="photo" role="img" aria-label="Warm lit bedroom suite with fireplace" style="background:linear-gradient(180deg,#c49a5a 0%,#e0b060 40%,#b07838 70%,#8a5a2a 100%)"></div>
  <h3>Facility 3</h3>
  <p>Lorem ipsum dolor sit amet, consectetur adipisicing elit, sed do eiusmod tempor incididunt ut labore et dolore magna aliqua.</p>
</article>
<article class="facility" style="left:606px">
  <div class="photo" role="img" aria-label="Bedroom with four poster bed" style="background:linear-gradient(180deg,#4a3a30 0%,#6a5444 40%,#b49a7a 65%,#5a7a80 100%)"></div>
  <h3>Facility 4</h3>
  <p>Lorem ipsum dolor sit amet, consectetur adipisicing elit, sed do eiusmod tempor incididunt ut labore et dolore magna aliqua.</p>
</article>

<div class="abs bottom-bar">2011 © www.tuskhollowlodge-mw.example | All rights reserved</div>

<ul class="abs footer-links">
  <li>Home</li><li>About Tusk Hollow</li><li>Rooms</li><li>Conferences</li><li>Cuisine</li><li>Facilities</li><li>Your Safari</li><li>Activities</li><li>Rates &amp; Special Offers</li><li>Booking Requests</li><li>Latest Developments</li><li>How To Get There</li>
</ul>

<div class="abs blog">
  <h4>Blog</h4>
  <p>Lorem ipsum dolor sit amet, consectetur adipisicing elit, sed do eiusmod tempor incididunt ut labore et dolore magna aliqua. <b>more</b></p>
  <p>Lorem ipsum dolor sit amet, consectetur adipisicing elit, sed do eiusmod tempor incididunt ut labore et dolore magna aliqua. <b>more</b></p>
  <p>Lorem ipsum dolor sit amet, consectetur adipisicing elit, sed do eiusmod tempor incididunt ut labore et dolore magna aliqua. <b>more</b></p>
</div>

<address class="abs office">
  <p>Booking Office :</p>
  <p>Tusk Hollow Lodge<br>Kalinde Estate,<br>Nsaluzi.Mpemba<br>P. O. Box 1180,<br>Mikolongwe, Malawi.</p>
  <p>Tel : +265 (0) 555 010 201<br>&nbsp;&nbsp;&nbsp;&nbsp;&nbsp;&nbsp;&nbsp;: +265 (0) 555 010 202<br>Fax : +265 (0) 1 555 019</p>
  <p>E-mail :info@tuskhollowlodge-mw.example<br>Website : www.tuskhollowlodge-mw.example</p>
</address>

<div class="abs circles" aria-hidden="true"><span></span><span></span><span></span><span></span><span></span></div>

</body>
</html>
```